Velmora Cabinets Letter Head and Email Signature

Hi
I would love a design package for a letterhead, email signature, even update my business card if you like if you can come up with a great idea for my new high end cabinet shop. Velmora Cabinets brings timeless craftsmanship to modern interiors, specializing in high end, custom cabinetry designed for architects and interior designers.

Target Market(s)

high end, luxury market

Industry/Entity Type

cabinet making

Requirements
Must have
• my colours of logo as the theme

```html
<!DOCTYPE html>
<html lang="en">
<head>
<meta charset="utf-8">
<title>Velmora Cabinets – Letterhead and Email Signature</title>
<link rel="stylesheet" href="https://fonts.googleapis.com/css2?family=Montserrat:wght@400;500;700&family=Source+Sans+3:wght@400&display=swap">
<style>
  :root {
    --backdrop: #afafaf;
    --paper: #ffffff;
    --brand-green: #4a7a40;
    --ink: #2b2b2b;
    --body-ink: #4a4a4a;
  }
  * { margin: 0; padding: 0; box-sizing: border-box; }
  html, body { width: 1200px; height: 795px; overflow: hidden; }
  body {
    position: relative;
    background: var(--backdrop);
    font-family: "Source Sans 3", "Helvetica Neue", Arial, sans-serif;
    color: var(--ink);
  }

  /* Shared wordmark */
  .brand {
    position: absolute; display: flex; align-items: center;
    font-family: "Montserrat", sans-serif; font-weight: 500;
    color: var(--brand-green); white-space: nowrap;
  }
  .brand-mark { background: var(--brand-green); flex: none; }

  /* Letterhead */
  .letterhead {
    position: absolute; left: 160px; top: 137px;
    width: 368px; height: 521px; background: var(--paper);
  }
  .letterhead .brand { left: 35px; top: 27px; font-size: 11px; letter-spacing: 0.3px; gap: 6px; }
  .letterhead .brand-mark { width: 12px; height: 12px; }

  .contact-block {
    position: absolute; left: 227px; top: 24px;
    border-left: 1px solid var(--brand-green);
    padding-left: 9px;
    font-family: "Montserrat", sans-serif; font-size: 6.6px; line-height: 9px;
    color: var(--ink);
  }
  .contact-line { display: flex; align-items: center; gap: 3px; white-space: nowrap; }
  .contact-line svg { flex: none; }

  .recipient { position: absolute; left: 35px; top: 122px; }
  .recipient-name { font-size: 7px; line-height: 10px; font-weight: 400; color: var(--ink); }
  .recipient-detail { font-size: 5.2px; line-height: 9px; color: var(--body-ink); }

  .letter-body {
    position: absolute; left: 35px; top: 185px; width: 299px;
    font-size: 5.3px; line-height: 9.1px; color: var(--body-ink);
    text-align: justify;
  }
  .letter-body p + p { margin-top: 7.6px; }

  .sign-off { position: absolute; left: 35px; top: 386px; color: var(--body-ink); }
  .sign-off-closing { font-size: 6px; line-height: 9px; }
  .sign-off-name { font-size: 7px; line-height: 10px; margin-top: 20px; }

  /* Email signature */
  .email-signature {
    position: absolute; left: 587px; top: 316px;
    width: 453px; height: 163px; background: var(--paper);
  }
  .email-signature .brand { left: 40px; top: 73px; font-size: 14.5px; gap: 8px; letter-spacing: 0; }
  .email-signature .brand-mark { width: 14px; height: 14px; }
  .signature-divider {
    position: absolute; left: 226px; top: 36px;
    width: 1.2px; height: 91px; background: var(--brand-green);
  }
  .signature-details { position: absolute; left: 250px; top: 34px; font-family: "Montserrat", sans-serif; }
  .signature-name { font-size: 18.5px; font-weight: 700; color: var(--brand-green); line-height: 22px; }
  .signature-role { font-size: 11px; color: var(--ink); line-height: 14px; margin-top: 2px; }
  .signature-contacts { margin-top: 14px; font-size: 11px; line-height: 15.8px; color: var(--ink); }
  .signature-contacts .contact-line { gap: 5px; }
</style>
</head>
<body>

<section class="letterhead" aria-label="Letterhead">
  <div class="brand"><span class="brand-mark"></span>Velmora Cabinets</div>

  <div class="contact-block">
    <div class="contact-line">
      <svg width="5" height="5" viewBox="0 0 10 10"><path fill="#4a7a40" d="M1 3c0-1.5 8-1.5 8 0v1H7V3H3v1H1zM2.5 5h5l1 4h-7z"/></svg>
      0491 570 110
    </div>
    <div class="contact-line">
      <svg width="5" height="5" viewBox="0 0 10 8"><rect x="0" y="0.5" width="10" height="7" fill="#4a7a40"/><path d="M0 .8l5 3.6 5-3.6" stroke="#fff" stroke-width="1" fill="none"/></svg>
      info@velmoracabinets.com.au
    </div>
    <div class="contact-line">
      <svg width="5" height="5" viewBox="0 0 10 10"><circle cx="5" cy="5" r="4" fill="none" stroke="#4a7a40" stroke-width="1.4"/></svg>
      @velmora.cabinets
    </div>
  </div>

  <div class="recipient">
    <div class="recipient-name">ELISE MARWOOD</div>
    <div class="recipient-detail">Chief Executive Officer</div>
    <div class="recipient-detail">City/State, Zip Code</div>
  </div>

  <div class="letter-body">
    <p>Thank you for considering Velmora Cabinets for your upcoming residential project. We design and build bespoke cabinetry for kitchens, dressing rooms, libraries and living spaces, working closely with architects and interior designers from first sketch to final installation. Every piece is made to measure in our own workshop, using carefully selected timbers, refined veneers and premium hardware. Our team pays close attention to proportion, joinery and finish, so that each cabinet feels calm, precise and built to last for generations.</p>
    <p>Following our recent meeting, we have prepared initial drawings and a material palette for your review. The proposal includes oak veneer joinery, soft close drawers, integrated lighting and concealed storage throughout the main living areas. We would welcome your feedback on finishes and layout before we prepare detailed shop drawings and confirm a production schedule that suits your timeline.</p>
    <p>Please feel free to contact me directly with any questions about the proposal, pricing or lead times. We look forward to working with you and your team, and to creating cabinetry that brings lasting quality, warmth and character to the finished interior. Samples of our timber and stone finishes can be delivered to your studio on request at any time this month.</p>
  </div>

  <div class="sign-off">
    <div class="sign-off-closing">Sincerely,</div>
    <div class="sign-off-name">Tomas Reyne</div>
  </div>
</section>

<section class="email-signature" aria-label="Email signature">
  <div class="brand"><span class="brand-mark"></span>Velmora Cabinets</div>
  <div class="signature-divider"></div>
  <div class="signature-details">
    <div class="signature-name">Daniel Hartvig</div>
    <div class="signature-role">Director Craftsman</div>
    <div class="signature-contacts">
      <div class="contact-line">
        <svg width="9" height="9" viewBox="0 0 10 10"><path fill="#4a7a40" d="M1 3c0-1.5 8-1.5 8 0v1H7V3H3v1H1zM2.5 5h5l1 4h-7z"/></svg>
        0491 570 110
      </div>
      <div class="contact-line">
        <svg width="9" height="8" viewBox="0 0 10 8"><rect x="0" y="0.5" width="10" height="7" fill="#4a7a40"/><path d="M0 .8l5 3.6 5-3.6" stroke="#fff" stroke-width="1" fill="none"/></svg>
        info@velmoracabinets.com.au
      </div>
      <div class="contact-line">
        <svg width="9" height="9" viewBox="0 0 10 10"><circle cx="5" cy="5" r="4" fill="none" stroke="#4a7a40" stroke-width="1.3"/></svg>
        @velmora.cabinets
      </div>
    </div>
  </div>
</section>

</body>
</html>
```